Real estate broker business card

Want a modern celan but effective business card for my residential and commercial real estate business. I want the back of the card to advertise my services and to capture business. I have attached the back of my current business card fore ideas
Updates

Logos, photo and text updates added! Added Saturday, September 3, 2016

Project Deadline Extended Reason: LOGOS, PHOTOS AND TEST JUST UPLOADED! I'M READY TO PICK A DESIGN! THANK YOU! Added Saturday, September 3, 2016

Target Market(s)

home buyers and seller. commercial buyers and sellers

Industry/Entity Type

Real Estate

Contact Information for Business Card

must have my contact information and my photo

Requirements
Must have
• Carla Ventrino
• Owner & Qualifying Broker
• Ventrino Real Estate Services
• 505.718.2094
• carla@ventrinohomes.example
• www.ventrinohomes.example
Nice to have
• metallic
• Business capture text: " Don't buy or lease property without someone looking out for your best interests. I will represent you on your home or investment purchase for FREE!"
• "Home owners, call today to receive a FREE market analysis for your homes value!

```html
<!DOCTYPE html>
<html lang="en">
<head>
<meta charset="utf-8">
<title>Ventrino Real Estate Services — Business Card</title>
<link rel="stylesheet" href="https://fonts.googleapis.com/css2?family=Cinzel:wght@400;600&family=Barlow+Semi+Condensed:wght@400;500&display=swap">
<style>
  :root {
    --page-bg: #e9ebec;
    --teal-light: #1b8d9c;
    --teal: #137a88;
    --teal-dark: #0b5a66;
    --silver: #d9dee0;
    --white: #ffffff;
    --ink-grey: #4a4a4a;
    --photo-tone-a: #5a4c42;
    --photo-tone-b: #c9b8ac;
  }
  * { box-sizing: border-box; margin: 0; padding: 0; }
  html, body {
    width: 1200px; height: 987px; overflow: hidden;
    background: var(--page-bg);
  }
  .card {
    position: absolute;
    left: 293px;
    width: 615px;
    height: 352px;
    overflow: hidden;
  }
  .card--front {
    top: 130px;
    background: radial-gradient(ellipse at 38% 45%, var(--teal-light) 0%, var(--teal) 45%, var(--teal-dark) 100%);
    color: var(--white);
  }
  .card--back {
    top: 505px;
    background: var(--white);
  }
  .portrait {
    position: absolute;
    left: 35px; top: 16px;
    width: 123px; height: 149px;
    border: 2px solid var(--white);
    border-radius: 8px;
    background: linear-gradient(160deg, var(--photo-tone-a) 0%, var(--photo-tone-b) 100%);
  }
  .agent-name {
    position: absolute;
    left: 36px; top: 178px;
    font-family: "Cinzel", serif;
    font-weight: 400;
    font-size: 24px;
    letter-spacing: 0.5px;
  }
  .agent-role {
    position: absolute;
    left: 36px; top: 208px;
    font-family: "Barlow Semi Condensed", sans-serif;
    font-weight: 500;
    font-size: 16px;
    line-height: 21px;
    text-transform: uppercase;
    letter-spacing: 0.3px;
  }
  .contact-list {
    position: absolute;
    left: 36px; top: 261px;
    list-style: none;
    font-family: "Barlow Semi Condensed", sans-serif;
    font-weight: 500;
    font-size: 16px;
    text-transform: uppercase;
    letter-spacing: 0.3px;
  }
  .contact-list li {
    display: flex; align-items: center;
    height: 23px;
  }
  .contact-list svg {
    width: 15px; height: 15px; margin-right: 8px; flex: none;
    fill: var(--white);
  }
  .brand-mark {
    position: absolute;
    left: 316px; top: 0;
    width: 276px; height: 352px;
    display: flex; flex-direction: column; align-items: center; justify-content: center;
    gap: 18px;
  }
  .brand-mark .dot {
    width: 22px; height: 22px; border-radius: 50%;
    background: var(--silver);
  }
  .brand-mark .brand-name {
    font-family: "Cinzel", serif;
    font-weight: 600;
    font-size: 40px;
    letter-spacing: 2px;
    color: var(--silver);
  }
  .back-brand {
    position: absolute;
    left: 0; right: 0; top: 158px;
    display: flex; align-items: center; justify-content: center;
    gap: 12px;
  }
  .back-brand .square {
    width: 26px; height: 26px;
    background: var(--teal);
  }
  .back-brand .brand-name {
    font-family: "Cinzel", serif;
    font-weight: 600;
    font-size: 26px;
    letter-spacing: 1px;
    color: var(--teal);
  }
  .offer {
    position: absolute;
    left: 0; right: 0; top: 269px;
    text-align: center;
    font-family: "Barlow Semi Condensed", sans-serif;
    font-weight: 500;
    font-size: 15px;
    line-height: 21px;
    text-transform: uppercase;
    color: var(--ink-grey);
  }
</style>
</head>
<body>
  <section class="card card--front">
    <div class="portrait" role="img" aria-label="Portrait photo of Carla Ventrino"></div>
    <h1 class="agent-name">Carla Ventrino</h1>
    <p class="agent-role">Owner &amp; Qualifying Broker<br>Ventrino Real Estate Services</p>
    <ul class="contact-list">
      <li>
        <svg viewBox="0 0 24 24" aria-hidden="true"><path d="M6.6 10.8a15.1 15.1 0 0 0 6.6 6.6l2.2-2.2a1 1 0 0 1 1-.25 11.4 11.4 0 0 0 3.6.57 1 1 0 0 1 1 1V20a1 1 0 0 1-1 1A17 17 0 0 1 3 4a1 1 0 0 1 1-1h3.5a1 1 0 0 1 1 1c0 1.25.2 2.45.57 3.57a1 1 0 0 1-.25 1z"/></svg>
        505.718.2094
      </li>
      <li>
        <svg viewBox="0 0 24 24" aria-hidden="true"><path d="M2 5h20v14H2z M3 6l9 7 9-7" fill="none" stroke="#fff" stroke-width="2"/></svg>
        carla@ventrinohomes.example
      </li>
      <li>
        <svg viewBox="0 0 24 24" aria-hidden="true"><circle cx="12" cy="12" r="10"/><path d="M4 12h16M12 2c3 3 3 17 0 20M12 2c-3 3-3 17 0 20" fill="none" stroke="#137a88" stroke-width="1.5"/></svg>
        www.ventrinohomes.example
      </li>
    </ul>
    <div class="brand-mark">
      <span class="dot"></span>
      <span class="brand-name">VENTRINO</span>
    </div>
  </section>

  <section class="card card--back">
    <div class="back-brand">
      <span class="square"></span>
      <span class="brand-name">Ventrino Real Estate Services</span>
    </div>
    <p class="offer">Home owners, call today to receive<br>a free market analysis for your homes value!</p>
  </section>
</body>
</html>
```